Laser Tattoo Removal Business Cards

We are looking for a professional business card design for a laser tattoo removal business. Ideally looking for a black business card design. The name of the business is Brightline Tattoo Removal. We place our cards at local tattoo shops so we ideally are looking for something trendy/edgy to draw both male and female clientele in.

Target Market(s)

Male/Female ages 18-60

Contact Information for Business Card

black background ideally.. hoping to stay within greys, whites and black

Font styles to use
Serif
Sans Serif

Colors
121212
a9a9a9
5c5c5c
f5f5f5
ffffff
7f7f7f
606060
848484
9d9d9d

Requirements
Must have
• Employee Info:
• Melissa Thornbury
• Chief Executive Offer
• m: 919.537.2846
• w: 919.362.4178
• f: 919.685.3907
• mthornbury@brightlinetattooremoval.example
• Address:
• 4615 Oakmere Pkwy, Suite 210
• Raleigh, NC 27654
• Website:
• www.brightlinetattooremoval.example
Nice to have
• Myabe business name on back or logo on back and employee info on the front

```html
<!DOCTYPE html>
<html lang="en">
<head>
<meta charset="utf-8">
<title>Brightline Tattoo Removal — Business Cards</title>
<link href="https://fonts.googleapis.com/css2?family=Oswald:wght@300;400&family=Figtree:wght@400;600;700&display=swap" rel="stylesheet">
<style>
  :root {
    --ink: #121212;
    --charcoal: #1e1d1b;
    --grey-dark: #5c5c5c;
    --grey-mid: #7f7f7f;
    --grey-soft: #9d9d9d;
    --grey-light: #a9a9a9;
    --paper: #f5f5f5;
    --white: #ffffff;
    --stage-left: #d2d2d2;
    --stage-right: #8a8a8a;
  }
  * { margin: 0; padding: 0; box-sizing: border-box; }
  html, body { width: 1200px; height: 960px; overflow: hidden; }
  body {
    position: relative;
    background: linear-gradient(90deg, var(--stage-left), var(--stage-right));
    font-family: "Figtree", Arial, sans-serif;
  }
  .card { position: absolute; width: 600px; height: 343px; overflow: hidden; }

  /* Front */
  .card--front { left: 302px; top: 122px; background: var(--white); }
  .card__pattern { position: absolute; inset: 0; }
  .card__pattern--light { background: radial-gradient(circle at 50% 45%, var(--white), #efefef); }
  .person__name {
    position: absolute; left: 43px; top: 138px;
    font-family: "Oswald", "Arial Narrow", sans-serif; font-weight: 400;
    font-size: 38px; line-height: 44px; color: #2a2a2a; letter-spacing: 0.2px;
    transform: scaleX(0.82); transform-origin: left;
  }
  .person__title {
    position: absolute; left: 43px; top: 181px;
    font-size: 13.5px; font-weight: 700; color: var(--grey-mid); letter-spacing: 0.2px;
  }
  .card__rule { position: absolute; left: 45px; top: 210px; width: 518px; height: 1px; background: #222; }
  .contact, .address {
    position: absolute; top: 228px;
    font-size: 13.5px; line-height: 18px; color: var(--grey-dark); list-style: none;
  }
  .contact { left: 44px; }
  .address { right: 37px; text-align: right; }
  .footer__strip { position: absolute; left: 0; bottom: 0; width: 330px; height: 11px; background: var(--grey-mid); }
  .footer__band {
    position: absolute; right: 0; bottom: 0; width: 294px; height: 42px;
    background: var(--charcoal); clip-path: polygon(31px 0, 100% 0, 100% 100%, 0 100%);
  }
  .footer__url {
    position: absolute; right: 10px; bottom: 12px;
    font-size: 13px; color: var(--white); letter-spacing: 0.1px;
  }
  .footer__url b { font-weight: 700; }

  /* Back */
  .card--back { left: 299px; top: 495px; background: var(--ink); }
  .card__pattern--dark { background: radial-gradient(circle at 50% 45%, #262626, var(--ink) 75%); }
  .brand {
    position: absolute; left: 0; right: 0; top: 152px; text-align: center;
    font-family: "Oswald", "Arial Narrow", sans-serif; font-weight: 300;
    font-size: 30px; letter-spacing: 4px; color: var(--paper); text-transform: uppercase;
  }
</style>
</head>
<body>
  <section class="card card--front" aria-label="Business card front">
    <div class="card__pattern card__pattern--light" role="img" aria-label="Faint light grey damask pattern background"></div>
    <h1 class="person__name">MELISSA THORNBURY</h1>
    <p class="person__title">CHIEF EXECUTIVE OFFER</p>
    <div class="card__rule"></div>
    <ul class="contact">
      <li>919.537.2846 (m)</li>
      <li>919.362.4178 (w)</li>
      <li>919.685.3907 (f)</li>
      <li>mthornbury@brightlinetattooremoval.example</li>
    </ul>
    <ul class="address">
      <li>4615 Oakmere Pkwy</li>
      <li>Suite 210</li>
      <li>Raleigh, NC 27654</li>
    </ul>
    <div class="footer__strip"></div>
    <div class="footer__band"></div>
    <p class="footer__url"><b>BRIGHTLINETATTOOREMOVAL</b>.example</p>
  </section>

  <section class="card card--back" aria-label="Business card back">
    <div class="card__pattern card__pattern--dark" role="img" aria-label="Subtle dark damask pattern background"></div>
    <p class="brand">Brightline Tattoo Removal</p>
  </section>
</body>
</html>
```